Tech business card design

We need an amazing business card design for our new business 'Pexla' a marketing tech startup based in Sydney, Australia. We provide an online marketplace for businesses to search and buy advertising media, connect with service providers and learn more about marketing. We wish to communicate 'cool tech', reliability and professionalism and design based around our logo.

Target Market(s)

Business Owners

Contact Information for Business Card

Name
Position
Email Address
Website
Phone Number

Font styles to use
Other font styles liked:
• Avenir & Avenir Next

Colors

Designer to choose colors to be used in the design.

```html
<!DOCTYPE html>
<html lang="en">
<head>
<meta charset="utf-8">
<title>Pexla Business Card</title>
<link href="https://fonts.googleapis.com/css2?family=Nunito+Sans:wght@400;700;900&display=swap" rel="stylesheet">
<style>
  :root {
    --navy: #1c2250;
    --navy-soft: #262d5e;
    --paper: #ffffff;
    --backdrop: #eeeeee;
    --ink-muted: #555a70;
    --pattern-light: #f3f3f5;
    --pattern-mid: #e9e9ee;
  }
  * { margin: 0; padding: 0; box-sizing: border-box; }
  html, body {
    width: 1200px; height: 800px; overflow: hidden;
    background: var(--backdrop);
    font-family: "Nunito Sans", "Avenir Next", Arial, sans-serif;
  }
  .stage {
    width: 1200px; height: 800px;
    display: flex; align-items: center; justify-content: center; gap: 60px;
  }
  .card {
    width: 500px; height: 286px;
    position: relative; overflow: hidden;
    box-shadow: 0 2px 6px rgba(0,0,0,0.12);
  }
  /* Front */
  .card-front { background: var(--paper); }
  .card-front .icon-pattern {
    position: absolute; inset: 0;
    background: linear-gradient(135deg, var(--pattern-light), var(--pattern-mid));
    opacity: 0.7;
  }
  .brand-name {
    position: absolute; left: 34px; top: 30px;
    font-weight: 900; font-size: 62px; letter-spacing: -1px;
    color: var(--navy); line-height: 1;
  }
  .divider {
    position: absolute; left: 0; right: 0; top: 126px;
    height: 1.5px; background: var(--navy);
  }
  .person {
    position: absolute; left: 150px; top: 100px;
  }
  .person-name {
    font-weight: 700; font-size: 18px; letter-spacing: 0.5px;
    color: var(--navy); text-transform: uppercase; line-height: 24px;
  }
  .person-role {
    margin-top: 4px; font-size: 12px; color: var(--ink-muted);
  }
  .contact-list {
    position: absolute; right: 24px; bottom: 26px;
    list-style: none; text-align: right;
  }
  .contact-item {
    display: flex; align-items: center; justify-content: flex-end; gap: 8px;
    font-size: 12px; color: var(--ink-muted); line-height: 20px;
  }
  .contact-icon { width: 12px; height: 12px; flex: none; }
  /* Back */
  .card-back {
    background: var(--navy);
    display: flex; align-items: center; justify-content: center;
  }
  .card-back .wordmark-pattern {
    position: absolute; inset: 0;
    background: linear-gradient(160deg, var(--navy-soft), var(--navy));
  }
  .back-name {
    position: relative;
    font-weight: 900; font-size: 38px; color: var(--paper); letter-spacing: -0.5px;
  }
</style>
</head>
<body>
<main class="stage">
  <section class="card card-front">
    <div class="icon-pattern" role="img" aria-label="Faint line-icon pattern of marketing symbols: charts, documents, megaphone, gears"></div>
    <div class="brand-name">pexla</div>
    <div class="divider"></div>
    <div class="person">
      <p class="person-name">Marcus Lane</p>
      <p class="person-role">Managing Director</p>
    </div>
    <ul class="contact-list">
      <li class="contact-item">000-987-6543
        <svg class="contact-icon" viewBox="0 0 12 12"><rect width="12" height="12" rx="2" fill="#1c2250"/><path d="M4 3h1.5l.6 1.7-.9.6a4 4 0 0 0 1.5 1.5l.6-.9L9 6.5V8c-3 .3-5.3-2-5-5z" fill="#fff"/></svg>
      </li>
      <li class="contact-item">info@pexlamail.com
        <svg class="contact-icon" viewBox="0 0 12 12"><rect width="12" height="12" rx="2" fill="#1c2250"/><rect x="2.5" y="3.5" width="7" height="5" fill="none" stroke="#fff" stroke-width="0.9"/><path d="M2.5 3.5 6 6.5l3.5-3" fill="none" stroke="#fff" stroke-width="0.9"/></svg>
      </li>
      <li class="contact-item">www.pexlamail.com
        <svg class="contact-icon" viewBox="0 0 12 12"><circle cx="6" cy="6" r="6" fill="#1c2250"/><circle cx="6" cy="6" r="3.5" fill="none" stroke="#fff" stroke-width="0.8"/><path d="M2.5 6h7M6 2.5c-1.5 2-1.5 5 0 7M6 2.5c1.5 2 1.5 5 0 7" fill="none" stroke="#fff" stroke-width="0.7"/></svg>
      </li>
    </ul>
  </section>

  <section class="card card-back">
    <div class="wordmark-pattern" role="img" aria-label="Tone-on-tone navy repeat pattern of the brand name"></div>
    <div class="back-name">pexla</div>
  </section>
</main>
</body>
</html>
```